Alliance Holiday Card thanking supporters

- Use a vertical (not horizontal) layout.

- On the front, use a few dozen small boxes (no smaller than .2x.2, no bigger than .3x.3) with pictures of different principals. On top of the boxes, a large map of Chicago, with dots for every principal we’re directly supporting through KRM, PLCs, coaching, BWT, etc. this year. Data for map will be sent on a different day.

- On the inside: Thanks to you, The Harrowgate Civic Alliance directly supports XXX public school principals across Chicago.

On behalf of our city’s best educators,
happy holidays!

We look forward to our continued partnership in the year ahead.

Target Market(s)

Funders and supporters

Industry/Entity Type

Education

Font styles to use
Sans Serif

Requirements
Must have
• Picture of principals and map
Nice to have
• dots on map
Should not have
• Our logo colors are red, gray and white.

```html
<!DOCTYPE html>
<html lang="en">
<head>
<meta charset="utf-8">
<title>Harrowgate Civic Alliance Holiday Card</title>
<link href="https://fonts.googleapis.com/css2?family=EB+Garamond:wght@400;500&family=Roboto+Condensed:wght@700&display=swap" rel="stylesheet">
<style>
  :root {
    --frame-gray: #8f9093;
    --paper: #ffffff;
    --brand-red: #b01e3a;
    --text-gray: #7d7d80;
    --photo-gray: #8d8e91;
    --ornament-gray: #b9b9bc;
    --tone-deep: #5a3a2a;
    --tone-brown: #8a5a3e;
    --tone-tan: #c08d6c;
    --tone-light: #d9ab8e;
    --tone-pale: #e3bea5;
    --cloth-dark: #2c2f3a;
    --cloth-light: #e4e4e6;
    --cloth-pink: #b04a8a;
    --cloth-teal: #3bb3b0;
  }
  * { margin: 0; padding: 0; box-sizing: border-box; }
  html, body { width: 1200px; height: 892px; overflow: hidden; background: var(--paper); }
  .spread { position: relative; width: 1200px; height: 892px; }

  .panel { position: absolute; top: 0; height: 892px; background: var(--frame-gray); }
  .panel--inside { left: 0; width: 576px; }
  .panel--front { left: 623px; width: 577px; }
  .panel__sheet { position: absolute; top: 12px; bottom: 13px; background: var(--paper); }
  .panel--inside .panel__sheet { left: 12px; right: 10px; }
  .panel--front .panel__sheet { left: 12px; right: 11px; }

  /* Inside message */
  .message {
    position: absolute; left: 0; right: 0; top: 540px;
    text-align: center; font-family: "EB Garamond", serif; color: var(--text-gray);
  }
  .message__lead {
    font-size: 35px; font-weight: 400; color: var(--brand-red); line-height: 40px;
  }
  .message__body {
    font-size: 14px; line-height: 24px; margin: 0 auto; width: 450px;
  }
  .message__ornament {
    display: block; width: 94px; height: 6px; margin: 10px auto 0;
    background: var(--ornament-gray); border-radius: 3px;
  }
  .message__kicker {
    font-family: "Roboto Condensed", sans-serif; font-weight: 700;
    font-size: 15.5px; line-height: 20px; margin-top: 17px; text-transform: uppercase;
  }
  .message__greeting {
    font-size: 35px; font-weight: 400; color: var(--brand-red); line-height: 40px; margin-top: 0;
  }
  .message__closing { font-size: 14px; line-height: 20px; margin-top: 6px; }

  /* Front */
  .wordmark {
    position: absolute; left: 200px; top: 66px; width: 156px;
    transform: rotate(180deg);
    font-family: "EB Garamond", serif; font-weight: 500;
    font-size: 25px; line-height: 1.05; color: var(--brand-red); text-align: left;
  }
  .principal-grid {
    position: absolute; left: 2px; right: 0; top: 435px; bottom: 0;
    display: grid; grid-template-columns: repeat(8, 1fr); grid-template-rows: repeat(5, 1fr);
    gap: 2px;
  }
  .principal-photo {
    --tone: var(--tone-tan); --cloth: var(--cloth-dark);
    background: linear-gradient(180deg, var(--photo-gray) 0%, var(--photo-gray) 15%, var(--tone) 55%, var(--cloth) 100%);
  }
  .principal-photo:nth-child(5n+1) { --tone: var(--tone-deep); }
  .principal-photo:nth-child(5n+2) { --tone: var(--tone-light); }
  .principal-photo:nth-child(5n+3) { --tone: var(--tone-brown); }
  .principal-photo:nth-child(5n+4) { --tone: var(--tone-pale); }
  .principal-photo:nth-child(3n+2) { --cloth: var(--cloth-light); }
  .principal-photo:nth-child(7n+5) { --cloth: var(--cloth-pink); }
  .principal-photo:nth-child(11n+6) { --cloth: var(--cloth-teal); }
</style>
</head>
<body>
<main class="spread">
  <section class="panel panel--inside">
    <div class="panel__sheet">
      <div class="message">
        <h1 class="message__lead">Thanks to you,</h1>
        <p class="message__body">The Harrowgate Civic Alliance directly supports XXX public school principals across Chicago.</p>
        <span class="message__ornament" role="img" aria-label="Decorative flourish divider"></span>
        <p class="message__kicker">On behalf of our city’s best educators,</p>
        <h2 class="message__greeting">Happy Holidays!</h2>
        <p class="message__closing">We look forward to your continued partnership in the year ahead.</p>
      </div>
    </div>
  </section>

  <section class="panel panel--front">
    <div class="panel__sheet">
      <div class="wordmark">The Harrowgate Civic Alliance</div>
      <div class="principal-grid">
        <div class="principal-photo" role="img" aria-label="Portrait photo of a school principal"></div>
        <div class="principal-photo" role="img" aria-label="Portrait photo of a school principal"></div>
        <div class="principal-photo" role="img" aria-label="Portrait photo of a school principal"></div>
        <div class="principal-photo" role="img" aria-label="Portrait photo of a school principal"></div>
        <div class="principal-photo" role="img" aria-label="Portrait photo of a school principal"></div>
        <div class="principal-photo" role="img" aria-label="Portrait photo of a school principal"></div>
        <div class="principal-photo" role="img" aria-label="Portrait photo of a school principal"></div>
        <div class="principal-photo" role="img" aria-label="Portrait photo of a school principal"></div>
        <div class="principal-photo" role="img" aria-label="Portrait photo of a school principal"></div>
        <div class="principal-photo" role="img" aria-label="Portrait photo of a school principal"></div>
        <div class="principal-photo" role="img" aria-label="Portrait photo of a school principal"></div>
        <div class="principal-photo" role="img" aria-label="Portrait photo of a school principal"></div>
        <div class="principal-photo" role="img" aria-label="Portrait photo of a school principal"></div>
        <div class="principal-photo" role="img" aria-label="Portrait photo of a school principal"></div>
        <div class="principal-photo" role="img" aria-label="Portrait photo of a school principal"></div>
        <div class="principal-photo" role="img" aria-label="Portrait photo of a school principal"></div>
        <div class="principal-photo" role="img" aria-label="Portrait photo of a school principal"></div>
        <div class="principal-photo" role="img" aria-label="Portrait photo of a school principal"></div>
        <div class="principal-photo" role="img" aria-label="Portrait photo of a school principal"></div>
        <div class="principal-photo" role="img" aria-label="Portrait photo of a school principal"></div>
        <div class="principal-photo" role="img" aria-label="Portrait photo of a school principal"></div>
        <div class="principal-photo" role="img" aria-label="Portrait photo of a school principal"></div>
        <div class="principal-photo" role="img" aria-label="Portrait photo of a school principal"></div>
        <div class="principal-photo" role="img" aria-label="Portrait photo of a school principal"></div>
        <div class="principal-photo" role="img" aria-label="Portrait photo of a school principal"></div>
        <div class="principal-photo" role="img" aria-label="Portrait photo of a school principal"></div>
        <div class="principal-photo" role="img" aria-label="Portrait photo of a school principal"></div>
        <div class="principal-photo" role="img" aria-label="Portrait photo of a school principal"></div>
        <div class="principal-photo" role="img" aria-label="Portrait photo of a school principal"></div>
        <div class="principal-photo" role="img" aria-label="Portrait photo of a school principal"></div>
        <div class="principal-photo" role="img" aria-label="Portrait photo of a school principal"></div>
        <div class="principal-photo" role="img" aria-label="Portrait photo of a school principal"></div>
        <div class="principal-photo" role="img" aria-label="Portrait photo of a school principal"></div>
        <div class="principal-photo" role="img" aria-label="Portrait photo of a school principal"></div>
        <div class="principal-photo" role="img" aria-label="Portrait photo of a school principal"></div>
        <div class="principal-photo" role="img" aria-label="Portrait photo of a school principal"></div>
        <div class="principal-photo" role="img" aria-label="Portrait photo of a school principal"></div>
        <div class="principal-photo" role="img" aria-label="Portrait photo of a school principal"></div>
        <div class="principal-photo" role="img" aria-label="Portrait photo of a school principal"></div>
        <div class="principal-photo" role="img" aria-label="Portrait photo of a school principal"></div>
      </div>
    </div>
  </section>
</main>
</body>
</html>
```